Leadership Training Business Needs a business card design

We need a business card designed for our company based in Auckland, New Zealand called Harbour Pathway Advisors. We conduct a variety of residential programmes that provide for differnet management levels. These programmes are designed to familiarise managers with important leadership concepts and techniques. This learning is reinforced through the provision of real workplace feedback and the use of action learning opportunities (experiential exercises) to develop the participants' leadership skills and potential. We would like to add our tag line which is:
Inspires Direction - Instils Values - Delivers Results
We would like the card to be a white background but would consider a different background colour on the back. Possibly include the following words on the back:
- Organisational Development
- Positive Cultural Change
- Leadership Programmes
- Practical Development "Tools"
- Crew Rhythm Inventory
- 360o degree Assessments
- Strengths Based Training
- Coaching and Mentoring

• Company Name, logo, contact details, website address and email.
• Persons name and their title

```html
<!DOCTYPE html>
<html lang="en">
<head>
<meta charset="utf-8">
<title>Harbour Pathway Advisors – Business Card</title>
<link href="https://fonts.googleapis.com/css2?family=Open+Sans:ital,wght@0,400;0,700;1,400&display=swap" rel="stylesheet">
<style>
  :root {
    --page: #ededed;
    --card: #ffffff;
    --card-edge: #cfcfcf;
    --orange: #f7a51e;
    --orange-deep: #f05a22;
    --yellow: #f4e51b;
    --green: #7dc242;
    --ink: #3b3b3b;
    --ink-soft: #555555;
  }
  html, body {
    margin: 0;
    width: 1200px;
    height: 1200px;
    overflow: hidden;
    background: var(--page);
    font-family: "Open Sans", Arial, sans-serif;
  }
  .canvas { position: relative; width: 1200px; height: 1200px; }
  .card {
    position: absolute;
    left: 176px;
    width: 848px;
    height: 484px;
    background: var(--card);
    outline: 1px solid var(--card-edge);
    overflow: hidden;
  }
  .card--front { top: 80px; }
  .card--back { top: 636px; background: var(--orange); }
  .card-art { position: absolute; inset: 0; width: 848px; height: 484px; }

  /* Front */
  .brand-mark {
    position: absolute; left: 384px; top: 44px;
    width: 80px; height: 80px; border-radius: 50%;
    background: var(--orange);
  }
  .company-name {
    position: absolute; left: 0; right: 0; top: 176px;
    text-align: center; font-size: 25px; color: var(--ink); margin: 0; font-weight: 400;
  }
  .company-sub {
    position: absolute; left: 0; right: 0; top: 204px;
    text-align: center; font-size: 24px; color: var(--orange); margin: 0;
  }
  .person-name {
    position: absolute; left: 0; right: 0; top: 272px;
    text-align: center; font-size: 23px; color: var(--ink-soft); margin: 0;
  }
  .person-title {
    position: absolute; left: 0; right: 0; top: 306px;
    text-align: center; font-size: 19px; font-style: italic; color: var(--ink-soft); margin: 0;
  }
  .tagline {
    position: absolute; left: 0; right: 0; top: 422px;
    text-align: center; font-size: 25px; font-weight: 700; color: #fff;
    letter-spacing: 0.5px; margin: 0;
  }

  /* Back */
  .service-list {
    position: absolute; left: 442px; top: 166px;
    margin: 0; padding: 0; list-style: none;
  }
  .service-list li {
    font-size: 19.5px; font-weight: 700; color: var(--orange);
    line-height: 36.5px; letter-spacing: 0.4px;
  }
  .back-mark {
    position: absolute; left: 122px; top: 314px;
    width: 72px; height: 72px; border-radius: 50%; background: #fff;
  }
  .back-name {
    position: absolute; left: 18px; width: 280px; top: 406px;
    text-align: center; color: #fff; font-size: 18px; line-height: 20px; margin: 0;
  }
</style>
</head>
<body>
<main class="canvas">

  <section class="card card--front" aria-label="Card front">
    <svg class="card-art" viewBox="0 0 848 484" aria-hidden="true">
      <defs>
        <linearGradient id="swoosh" x1="0" x2="1" y1="0" y2="0">
          <stop offset="0" stop-color="var(--green)"/>
          <stop offset="0.5" stop-color="var(--yellow)"/>
          <stop offset="1" stop-color="var(--orange-deep)"/>
        </linearGradient>
      </defs>
      <path d="M0,424 Q424,306 848,418 L848,432 Q424,318 0,440 Z" fill="url(#swoosh)"/>
      <path d="M0,450 Q424,320 848,452 L848,484 L0,484 Z" fill="var(--orange)"/>
    </svg>
    <div class="brand-mark" aria-hidden="true"></div>
    <h1 class="company-name">Harbour Pathway Advisors</h1>
    <p class="company-sub">Leadership Programmes</p>
    <p class="person-name">Persons Name</p>
    <p class="person-title">Title Name</p>
    <p class="tagline">Inspires Direction | Instils Values | Delivers Results</p>
  </section>

  <section class="card card--back" aria-label="Card back">
    <svg class="card-art" viewBox="0 0 848 484" aria-hidden="true">
      <defs>
        <linearGradient id="rim" x1="0" x2="0" y1="0" y2="1">
          <stop offset="0" stop-color="var(--green)"/>
          <stop offset="0.35" stop-color="var(--yellow)"/>
          <stop offset="0.7" stop-color="var(--orange)"/>
          <stop offset="1" stop-color="var(--orange-deep)"/>
        </linearGradient>
        <linearGradient id="rim-left" x1="0" x2="0" y1="0" y2="1">
          <stop offset="0" stop-color="var(--yellow)"/>
          <stop offset="1" stop-color="var(--orange-deep)"/>
        </linearGradient>
      </defs>
      <path d="M52,0 H660 L700,230 L386,200 Q170,130 0,190 V32 Z" fill="#fff"/>
      <ellipse cx="599" cy="284" rx="226" ry="312" fill="#fff"/>
      <path d="M693,0 A226,312 0 0 1 773,484" fill="none" stroke="url(#rim)" stroke-width="7"/>
      <path d="M381,200 A226,312 0 0 0 425,484" fill="none" stroke="url(#rim-left)" stroke-width="4"/>
    </svg>
    <ul class="service-list">
      <li>Organisational Development</li>
      <li>Positive Cultural Change</li>
      <li>Leadership Programmes</li>
      <li>Practical Development "Tools"</li>
      <li>Crew Rhythm Inventory</li>
      <li>360° degree Assessments</li>
      <li>Strengths Based Training</li>
      <li>Coaching and Mentoring</li>
    </ul>
    <div class="back-mark" aria-hidden="true"></div>
    <p class="back-name">Harbour Pathway Advisors<br>Leadership Programmes</p>
  </section>

</main>
</body>
</html>
```